New webdesign for a cable company

We need a new design for Lunor Media.

There exist a suggestion for the page, were we have attached files to show you this. The design here is not good enough, but here you can se what content we need.

You can feel free to give adjustment to this design to make it better, our blow us away with a new brilliant design, but from this design you see what content we need.

The important is that the company get a design who represent its products:
- TV = Cable TV
- Bredbånd = Broadband
- Mobil = Mobile phone
- Strøm = Electricity
- Alarm = Alarm
- Lunor Komplett = a cobain pagage of all our products.

Lunor Media would like costumers who visit the site to het the impression that Lunor Media is a professional, innovative and fun company.
Updates

We have to day uploaded pictures of the existing page as the link haven't been working for the most of you as it's placed on a server our developer are using and is often shut it down. 

We have also updated the brief with some new and updated description so please read true the updated brief. 

We will at the same time inform that we haven't been able to give feedback on any of the received design and are sorry for that, we will within the next 24 hours hopefully have started responded the different received designs.

Looking forward to see more suggestion and hope you will help us create and very professional and informative design. 

Reason: We have decided to extend the deadline due to the number of design suggestion who is sent in and your lack of response to all designers due to our own workload.

This project was unfortunately for different reason put on ice for a while, but we are now ready to complete the design and will answer and give feedback too all the received design suggestions. 

Within a couple of days we hope we have answered all you who sent us suggestions, we appreciate all suggestions and hope to get in more suggestions.

Reason: Deisgn description have been updated

Target Market(s)

Our costumer are both private and companies

Industry/Entity Type

Tv

Requirements
Must have
• A easy way to promote and inform about changes in our products, there are a constant change in our products and it must bee a easy and good way to changes ass the marked change. Cheek out this link, for a example of what we like/think of here, https://nett.fjordsignal.no

On all pages there must be a easy way to click on a order button and too inform about your interest (thats two different things), could be placed in the top right corner for example. In the order form you should follow a step by step part:
1. Cheek what product we can provide you.
2. Chooce products.
3. Costumer inforamtion.
4. Confirmation.

Somewere on the portal it must be possible for costumers to log on to their own administration, where they can cheek for invoices, other statuses, etc.

A main menu existing of:
Hjem (Home)
Produkter (Products)
Storkunde (key account/large costumers)
Kundeservice (Costumerservice)
Min side (My page)

The main menu should have the following sub titles:
- Under "Produkter"/products our different products must be listed
- Under "Kundeservice"/Costumerservice it must have these submenus:
- Hjelp og støtte = Help.
- Faktura = Invoice
- Brukerguider = Userguides
- Abbonementavtaler = Terms and conditions.

A bottom menu where we have 5 main categories, with sub categories:
Om oss (about us)
- Om Lunor Media (about Lunor Media)
- Kontaktinformajson ( contact information)
- Pressemeldinger (Pressrelese)
- Ledige stillinger (positions available)
- KRAV ( and organisastion in our field)

Produkter (Product)
- TV (TV)
- Bredbånd (Broadand)
- Telefoni (telephony, both mobil)
- Strøm (elecricity)
- Arlam (Alarm)

Borrettslag/Sameier (Housing cooperatives)
- Løsninger (solutions)
- Produkter (product)
- Kontaktpersoner (contactpersons)

Utbygger (developer)
- Hva vi kan gjøre for dere. (What we can do for you)

Opperatørnett (operators)

Build up the categories and bottom menu something like this:
https://nett.fjordsignal.no
www.brevix.com
Nice to have
• A main menu existing of:
Hjem (Home)
Produkter (Products)
Lunor Media
Kontakt oss (Contact us)

Under "Produkter"/products our different products must be listed and under "Kundeservice"/Costumerservice it must have these submenus:
- Hjelp og støtte = Help.
- Faktura = Invoice
Should not have
• Any translation section since the homepage only will be in Norwegian.

```html
<!DOCTYPE html>
<html lang="no">
<head>
<meta charset="utf-8">
<title>Lunor Media – Bestilling</title>
<link rel="stylesheet" href="https://fonts.googleapis.com/css2?family=Ubuntu:wght@400;500&family=Arimo:wght@400;700&display=swap">
<style>
  :root {
    --topbar: #000000;
    --white: #ffffff;
    --ink: #2f3338;
    --ink-soft: #555a60;
    --muted: #a4a8ad;
    --line: #e6e8ea;
    --field-border: #c9ccd0;
    --brand: #1f6fc0;
    --brand-light: #5fb3ea;
    --brand-mid: #3a97dc;
    --content-top: #e9eaeb;
    --content-bottom: #f5f5f5;
    --footer: #2a2a2a;
    --footer-head: #d2d4d6;
    --footer-text: #8a8d90;
    --footer-line: #3a3a3a;
  }
  * { box-sizing: border-box; margin: 0; padding: 0; }
  html, body { width: 1200px; height: 1012px; overflow: hidden; }
  body { background: var(--footer); font-family: "Arimo", Arial, sans-serif; position: relative; }

  .page { position: absolute; left: 0; top: 0; width: 1200px; height: 1012px; }

  /* Top bar */
  .topbar { position: absolute; left: 0; top: 0; width: 1200px; height: 38px; background: var(--topbar); }
  .social { position: absolute; left: 180px; top: 12px; display: flex; gap: 3px; }
  .social span { width: 13px; height: 13px; background: #6d7277; border-radius: 2px; }
  .quick-actions { position: absolute; right: 435px; top: 7px; display: flex; align-items: center; gap: 10px; }
  .login-link { font-size: 10px; color: #c9c9c9; display: flex; align-items: center; gap: 5px; margin-right: 6px; }
  .btn-small { height: 24px; padding: 0 12px; font-size: 10px; line-height: 22px; border-radius: 2px; }
  .btn-interest { border: 1px solid #6d7277; color: #d6d6d6; }
  .btn-order { background: linear-gradient(180deg, var(--brand-light), var(--brand-mid)); border: 1px solid #3388cc; color: var(--white); }
  .search-label { position: absolute; left: 777px; top: 13px; font-size: 10px; color: #c9c9c9; }
  .search-box { position: absolute; left: 841px; top: 7px; width: 177px; height: 25px; background: var(--white); border-radius: 2px; font-size: 10px; color: var(--muted); padding: 7px 8px; }
  .search-box svg { position: absolute; right: 8px; top: 8px; }

  /* Header */
  .header { position: absolute; left: 0; top: 38px; width: 1200px; height: 77px; background: var(--white); }
  .logo { position: absolute; left: 172px; top: 22px; display: flex; align-items: center; gap: 10px; font-family: "Ubuntu", sans-serif; font-size: 32px; color: var(--brand); }
  .logo i { width: 22px; height: 22px; border-radius: 50%; background: var(--brand); display: block; }
  .main-nav { position: absolute; right: 182px; top: 28px; display: flex; gap: 20px; }
  .nav-item { position: relative; font-family: "Ubuntu", sans-serif; }
  .nav-item b { display: block; font-weight: 400; font-size: 15px; color: var(--ink); letter-spacing: .2px; }
  .nav-item small { display: block; font-family: "Arimo", sans-serif; font-size: 9px; color: var(--ink-soft); margin-top: 2px; }
  .nav-item.active::before { content: ""; position: absolute; left: 0; right: 0; top: -28px; height: 3px; background: var(--brand); }

  /* Content */
  .content { position: absolute; left: 0; top: 115px; width: 1200px; height: 600px; background: linear-gradient(180deg, var(--content-top), var(--content-bottom)); }
  .steps { position: absolute; left: 178px; top: 16px; width: 840px; height: 36px; display: flex; background: var(--white); border: 1px solid #e1e3e5; }
  .step { flex: 1; display: flex; align-items: center; gap: 9px; padding-left: 22px; font-size: 11px; color: var(--muted); border-right: 1px solid var(--line); }
  .step:last-child { border-right: 0; }
  .step i { width: 18px; height: 18px; border-radius: 50%; border: 1px solid #c4c7ca; font-style: normal; font-size: 10px; text-align: center; line-height: 16px; }
  .step.done { color: var(--ink-soft); }
  .step.done i { border-color: var(--ink-soft); }
  .step.current { color: var(--brand); }
  .step.current i { background: var(--brand); border-color: var(--brand); color: var(--white); }

  .panel { position: absolute; top: 64px; height: 520px; background: var(--white); border: 1px solid #e1e3e5; }
  .panel-order { left: 178px; width: 469px; }
  .panel-summary { left: 656px; width: 362px; }
  .panel-title { position: absolute; font-family: "Ubuntu", sans-serif; font-weight: 400; font-size: 12px; color: var(--ink); letter-spacing: .5px; }

  .field-label { position: absolute; left: 58px; font-size: 11px; color: var(--ink-soft); transform: translateY(-50%); }
  .field { position: absolute; left: 163px; width: 211px; height: 25px; border: 2px solid var(--field-border); border-radius: 3px; transform: translateY(-50%); }
  .divider { position: absolute; height: 1px; background: var(--line); }
  .radio { position: absolute; display: flex; align-items: center; gap: 7px; font-size: 10px; color: var(--muted); transform: translateY(-50%); white-space: nowrap; }
  .radio i { width: 5px; height: 5px; border-radius: 50%; border: 1px solid #c4c7ca; display: block; }
  .radio.checked i { background: var(--ink); border-color: var(--ink); }
  .remark-box { position: absolute; left: 163px; top: 327px; width: 211px; height: 101px; border: 2px solid var(--field-border); border-radius: 3px; }

  .summary-text { position: absolute; font-size: 10px; color: var(--muted); transform: translateY(-50%); white-space: nowrap; }
  .qty-label { position: absolute; left: 191px; font-size: 11px; color: var(--ink-soft); transform: translateY(-50%); }
  .qty-box { position: absolute; left: 253px; width: 33px; height: 27px; border: 2px solid #d6d8db; border-radius: 3px; font-size: 10px; color: var(--muted); text-align: center; line-height: 23px; transform: translateY(-50%); }
  .send-btn { position: absolute; left: 219px; top: 456px; width: 107px; height: 39px; background: linear-gradient(180deg, var(--brand-light), var(--brand-mid)); border: 1px solid #3388cc; border-radius: 2px; color: #e8f4fc; font-size: 14px; text-align: center; line-height: 37px; }

  /* Footer */
  .footer { position: absolute; left: 0; top: 715px; width: 1200px; height: 297px; background: var(--footer); }
  .footer-menu { position: absolute; left: 178px; top: 30px; width: 840px; display: flex; }
  .footer-col { width: 168px; list-style: none; }
  .footer-col h3 { font-family: "Ubuntu", sans-serif; font-weight: 400; font-size: 12px; color: var(--footer-head); margin-bottom: 10px; letter-spacing: .3px; }
  .footer-col li { font-size: 11px; color: var(--footer-text); line-height: 20px; }
  .footer-rule { position: absolute; left: 178px; top: 210px; width: 840px; height: 1px; background: var(--footer-line); }
  .copyright { position: absolute; left: 178px; top: 228px; font-size: 10px; color: var(--footer-text); }
  .copyright b { color: #c4c6c8; font-weight: 400; }
</style>
</head>
<body>
  <div class="page">
    <div class="topbar">
      <div class="social"><span></span><span></span><span></span><span></span><span></span><span></span></div>
      <div class="quick-actions">
        <span class="login-link">
          <svg width="9" height="10" viewBox="0 0 9 10"><circle cx="4.5" cy="3" r="2.5" fill="#c9c9c9"/><path d="M0 10 C0 6.5 9 6.5 9 10 Z" fill="#c9c9c9"/></svg>
          Logg inn – Min side
        </span>
        <span class="btn-small btn-interest">Meld interesse</span>
        <span class="btn-small btn-order">Bestill nå</span>
      </div>
      <div class="search-label">Site Search:</div>
      <div class="search-box">Search:
        <svg width="6" height="8" viewBox="0 0 6 8"><path d="M0 0 L6 4 L0 8 Z" fill="#444"/></svg>
      </div>
    </div>

    <div class="header">
      <div class="logo"><i></i>Lunor Media</div>
      <nav class="main-nav">
        <div class="nav-item"><b>HJEM</b><small>Til forsiden</small></div>
        <div class="nav-item active"><b>PRODUKTER</b><small>TV, bredbånd, mobil</small></div>
        <div class="nav-item"><b>STORKUNDE</b><small>For bedrifter</small></div>
        <div class="nav-item"><b>KUNDESERVICE</b><small>Hjelp og faktura</small></div>
        <div class="nav-item"><b>MIN SIDE</b><small>Logg inn her</small></div>
      </nav>
    </div>

    <div class="content">
      <div class="steps">
        <div class="step done"><i>1</i>Sjekk hva vi kan levere</div>
        <div class="step done"><i>2</i>Velg produkter</div>
        <div class="step current"><i>3</i>Kundeinformasjon</div>
        <div class="step"><i>4</i>Bekreftelse</div>
      </div>

      <section class="panel panel-order">
        <h2 class="panel-title" style="left:58px;top:29px">ONLINE ORDER FORM</h2>
        <span class="field-label" style="top:75px">Name:</span><div class="field" style="top:75px"></div>
        <span class="field-label" style="top:114px">Email:</span><div class="field" style="top:114px"></div>
        <span class="field-label" style="top:153px">Phone:</span><div class="field" style="top:153px"></div>
        <span class="field-label" style="top:191px">Address:</span><div class="field" style="top:191px"></div>
        <div class="divider" style="left:58px;top:226px;width:374px"></div>
        <span class="field-label" style="top:250px">Products</span>
        <span class="radio checked" style="left:60px;top:275px"><i></i>TV</span>
        <span class="radio" style="left:153px;top:275px"><i></i>Bredbånd</span>
        <span class="radio" style="left:245px;top:275px"><i></i>Mobil</span>
        <span class="radio" style="left:338px;top:275px"><i></i>Strøm</span>
        <span class="radio" style="left:60px;top:300px"><i></i>Alarm</span>
        <span class="radio checked" style="left:153px;top:300px"><i></i>Lunor Komplett</span>
        <span class="field-label" style="top:331px">Remark:</span>
        <div class="remark-box"></div>
      </section>

      <section class="panel panel-summary">
        <h2 class="panel-title" style="left:23px;top:28px;font-size:11px">ORDER SUMMARY</h2>
        <span class="summary-text" style="left:23px;top:72px">TV</span>
        <span class="qty-label" style="top:72px">Quantity:</span><div class="qty-box" style="top:72px">1</div>
        <span class="summary-text" style="left:23px;top:124px">Lunor Komplett</span>
        <span class="qty-label" style="top:124px">Quantity:</span><div class="qty-box" style="top:124px">2</div>
        <div class="divider" style="left:23px;top:161px;width:283px"></div>
        <span class="summary-text" style="left:23px;top:194px">Maren Holt</span>
        <span class="summary-text" style="left:23px;top:221px">mholt@postmail.com</span>
        <span class="summary-text" style="left:23px;top:246px">55 510 2841</span>
        <span class="summary-text" style="left:23px;top:272px">4815 Harbor Lane, Suit 2291, Fairbrook, CA 95318</span>
        <div class="send-btn">Send</div>
      </section>
    </div>

    <footer class="footer">
      <div class="footer-menu">
        <ul class="footer-col"><h3>Om oss</h3><li>Om Lunor Media</li><li>Kontaktinformasjon</li><li>Pressemeldinger</li><li>Ledige stillinger</li><li>KRAV</li></ul>
        <ul class="footer-col"><h3>Produkter</h3><li>TV</li><li>Bredbånd</li><li>Telefoni</li><li>Strøm</li><li>Alarm</li></ul>
        <ul class="footer-col"><h3>Borettslag/Sameier</h3><li>Løsninger</li><li>Produkter</li><li>Kontaktpersoner</li></ul>
        <ul class="footer-col"><h3>Utbygger</h3><li>Hva vi kan gjøre for dere</li></ul>
        <ul class="footer-col"><h3>Operatørnett</h3></ul>
      </div>
      <div class="footer-rule"></div>
      <p class="copyright">© Copyright <b>Kestrel Works</b>. All Rights Reserved</p>
    </footer>
  </div>
</body>
</html>
```